MRT Property - Business Cards

Looking for a business card & general letterhead, signage etc design for our new logo.

Colours:
000a20
0056a2
00b5ef
0088ce
68cef2

Fonts:
Poppins
Karla

Please keep look and feel of new brand - example in the zip package I sent.

```html
<!DOCTYPE html>
<html lang="en">
<head>
<meta charset="utf-8">
<title>MRT Property – Business Cards</title>
<link rel="stylesheet" href="https://fonts.googleapis.com/css2?family=Poppins:wght@400;700&display=swap">
<style>
  :root {
    --stage: #232323;
    --card: #0b1120;
    --navy: #000a20;
    --brand-blue: #0056a2;
    --bright-blue: #00b5ef;
    --mid-blue: #0088ce;
    --light-blue: #68cef2;
    --white: #ffffff;
  }
  * { box-sizing: border-box; margin: 0; padding: 0; }
  html, body {
    width: 1200px; height: 781px; overflow: hidden;
    background: var(--stage);
    font-family: "Poppins", sans-serif;
  }
  .canvas { position: relative; width: 1200px; height: 781px; }
  .card {
    position: absolute;
    width: 540px; height: 310px;
    background: var(--card);
    border-radius: 26px;
    box-shadow: 0 4px 0 var(--bright-blue), 0 18px 30px rgba(0,0,0,.55);
    overflow: hidden;
  }
  .card--front { left: 70px; top: 90px; }
  .card--back { left: 590px; top: 380px; }

  .wordmark {
    display: flex; align-items: center; gap: 18px;
    position: absolute; left: 0; right: 0; top: 0; bottom: 0;
    justify-content: center;
  }
  .wordmark__dot {
    width: 46px; height: 46px; border-radius: 50%;
    background: var(--mid-blue);
  }
  .wordmark__name {
    font-weight: 700; font-size: 58px; color: var(--brand-blue);
    letter-spacing: 1px;
  }

  .back-decoration {
    position: absolute; left: 40px; top: 70px;
    width: 300px; height: 240px;
    border-radius: 160px 160px 0 0;
    background: radial-gradient(ellipse at 30% 80%, #2a3244 0%, #151c2c 55%, rgba(11,17,32,0) 80%);
  }

  .identity {
    position: absolute; right: 34px; top: 30px;
    text-align: right;
  }
  .identity__brand {
    display: flex; align-items: center; justify-content: flex-end; gap: 10px;
    font-weight: 700; font-size: 30px; color: var(--brand-blue);
  }
  .identity__brand-dot {
    width: 20px; height: 20px; border-radius: 50%; background: var(--mid-blue);
  }
  .identity__person {
    margin-top: 14px;
    border-right: 7px solid var(--brand-blue);
    padding-right: 10px;
  }
  .identity__name { font-weight: 700; font-size: 19px; color: var(--brand-blue); line-height: 1.1; }
  .identity__role { font-size: 13px; color: var(--white); }

  .contact {
    position: absolute; right: 34px; top: 150px;
    text-align: right; color: var(--white); font-size: 13px; line-height: 1.45;
  }
  .contact__address { margin-bottom: 10px; margin-right: 24px; }
  .contact__line { display: flex; align-items: center; justify-content: flex-end; gap: 8px; }
  .contact__icon { width: 14px; height: 14px; flex: none; }
</style>
</head>
<body>
<main class="canvas">
  <section class="card card--front" aria-label="Business card front">
    <div class="wordmark">
      <span class="wordmark__dot"></span>
      <span class="wordmark__name">MRT Property</span>
    </div>
  </section>

  <section class="card card--back" aria-label="Business card back">
    <div class="back-decoration" role="img" aria-label="Faint embossed brand shape"></div>

    <div class="identity">
      <div class="identity__brand">
        <span class="identity__brand-dot"></span>
        <span>MRT Property</span>
      </div>
      <div class="identity__person">
        <p class="identity__name">DANIEL REEVES</p>
        <p class="identity__role">Managing Director</p>
      </div>
    </div>

    <div class="contact">
      <p class="contact__address">Your address, City<br>State, Zip 1234</p>
      <p class="contact__line">123 456 789
        <svg class="contact__icon" viewBox="0 0 16 16"><path fill="#00b5ef" d="M3 1l3 3-1.5 2a9 9 0 0 0 5.5 5.5L12 10l3 3-2 2C7 15 1 9 1 3z"/></svg>
      </p>
      <p class="contact__line">info@youremail.com
        <svg class="contact__icon" viewBox="0 0 16 16"><rect x="1" y="3" width="14" height="10" rx="1" fill="#00b5ef"/><path d="M1 4l7 5 7-5" stroke="#0b1120" stroke-width="1.4" fill="none"/></svg>
      </p>
      <p class="contact__line">www.yourwebsite.com
        <svg class="contact__icon" viewBox="0 0 16 16"><circle cx="8" cy="8" r="7" fill="#00b5ef"/><path d="M1 8h14M8 1c-3 4-3 10 0 14M8 1c3 4 3 10 0 14" stroke="#0b1120" stroke-width="1.1" fill="none"/></svg>
      </p>
    </div>
  </section>
</main>
</body>
</html>
```